High Tech Real Estate Startup needs a business card

We are developing an innovative real estate marketing product based around advanced search and virtual reality.

We talk to people, we need business cards.

Target Market(s)

The target market is technology professionals and realtors.

Contact Information for Business Card

The information to be included will include

Name
Title
Phone Number
E-mail Address
www.zelquin.com

It should use simple iconography for each one of those fields.

Font styles to use
Other font styles liked:
• Co, Jubilat, Avenir

Colors

Designer to choose colors to be used in the design.

Requirements
Must have
• Clean aesthetic,
• Good use of negative space.
• It should use our company logo, shown in the attached file. It is able to use the negative of that logo (coloured font and white background) and I have attached other acceptable accent colours in a swatch file.
Should not have
• Should not be too busy
• No extraneous text (slogans, tag lines etc)

```html
<!DOCTYPE html>
<html lang="en">
<head>
<meta charset="utf-8">
<title>Zelquin Business Card</title>
<link rel="stylesheet" href="https://fonts.googleapis.com/css2?family=Montserrat:wght@500;600&family=Roboto:wght@400&display=swap">
<style>
  :root {
    --teal: #19b5bc;
    --charcoal: #232323;
    --charcoal-soft: #2e2e2e;
    --ink: #1c1c1c;
    --paper: #ffffff;
    --stage: #ecebea;
  }
  * { box-sizing: border-box; margin: 0; padding: 0; }
  html, body { width: 1200px; height: 930px; overflow: hidden; }
  body { background: var(--stage); position: relative; font-family: "Roboto", Arial, sans-serif; }

  .card {
    position: absolute;
    width: 580px;
    height: 332px;
    border-radius: 18px;
    overflow: hidden;
    box-shadow: 0 10px 30px rgba(0,0,0,0.18);
  }

  /* Back side */
  .card-back { left: 70px; top: 80px; background: var(--charcoal); }
  .card-back .network-art {
    position: absolute; inset: 0;
    background: radial-gradient(ellipse at 40% 45%, var(--charcoal-soft) 0%, var(--charcoal) 70%);
  }
  .card-back .wordmark {
    position: absolute; left: 0; right: 0; top: 50%;
    transform: translateY(-50%);
    text-align: center;
    font-family: "Montserrat", Arial, sans-serif;
    font-weight: 500;
    font-size: 66px;
    letter-spacing: 2px;
    color: var(--teal);
  }

  /* Front side */
  .card-front { left: 550px; top: 520px; background: var(--paper); }
  .card-front .wordmark {
    position: absolute; left: 38px; top: 132px;
    font-family: "Montserrat", Arial, sans-serif;
    font-weight: 500;
    font-size: 50px;
    letter-spacing: 1px;
    color: var(--teal);
  }
  .card-front .divider {
    position: absolute; left: 330px; top: 62px;
    width: 2px; height: 120px; background: var(--teal);
  }
  .contact { position: absolute; left: 350px; top: 52px; color: var(--ink); }
  .contact .name {
    font-family: "Montserrat", Arial, sans-serif;
    font-weight: 600; font-size: 17px; color: var(--teal);
    letter-spacing: 0.3px;
  }
  .contact .title { font-size: 13px; margin: 1px 0 6px 8px; }
  .contact .address { font-size: 13px; line-height: 16px; margin-left: 8px; margin-bottom: 6px; }
  .contact .line { display: flex; align-items: center; gap: 7px; font-size: 13px; line-height: 17px; margin-left: 8px; }
  .contact .line svg { width: 10px; height: 10px; flex: none; }
  .card-front .wave { position: absolute; inset: 0; width: 100%; height: 100%; }
</style>
</head>
<body>

  <section class="card card-back" aria-label="Card back">
    <div class="network-art" role="img" aria-label="Faint grey connected-dots network pattern"></div>
    <div class="wordmark">ZELQUIN</div>
  </section>

  <section class="card card-front" aria-label="Card front">
    <svg class="wave" viewBox="0 0 580 332" preserveAspectRatio="none" aria-hidden="true">
      <path d="M300 332 C 350 250, 430 250, 500 235 C 540 226, 565 210, 580 190 L580 332 Z" fill="var(--charcoal)"/>
      <path d="M292 332 C 340 246, 420 246, 494 230 C 535 221, 562 204, 580 182" fill="none" stroke="var(--paper)" stroke-width="7"/>
      <path d="M286 332 C 336 242, 416 242, 490 226 C 532 217, 560 200, 580 176" fill="none" stroke="var(--teal)" stroke-width="4"/>
    </svg>

    <div class="wordmark">ZELQUIN</div>
    <div class="divider"></div>

    <div class="contact">
      <div class="name">DANIEL REYES</div>
      <div class="title">Director</div>
      <div class="address">482 Maple Ridge Ln.<br>Franklin, TN 37064</div>
      <div class="line">
        <svg viewBox="0 0 10 10"><path d="M2 1 L4 1 L4.6 3 L3.4 3.8 C4 5.2 4.8 6 6.2 6.6 L7 5.4 L9 6 L9 8 C5 8.4 1.6 5 2 1 Z" fill="var(--teal)"/></svg>
        <span>+1-555-210-7381</span>
      </div>
      <div class="line">
        <svg viewBox="0 0 10 10"><rect x="0.8" y="2" width="8.4" height="6" fill="none" stroke="var(--teal)" stroke-width="1"/><path d="M1 2.3 L5 5.5 L9 2.3" fill="none" stroke="var(--teal)" stroke-width="1"/></svg>
        <span>info@zelquin.com</span>
      </div>
      <div class="line">
        <svg viewBox="0 0 10 10"><circle cx="5" cy="5" r="4" fill="none" stroke="var(--teal)" stroke-width="1"/><ellipse cx="5" cy="5" rx="1.8" ry="4" fill="none" stroke="var(--teal)" stroke-width="0.8"/><path d="M1 5 H9" stroke="var(--teal)" stroke-width="0.8"/></svg>
        <span>www.zelquin.com</span>
      </div>
    </div>
  </section>

</body>
</html>
```